KRTB

We want to design our company brochure. We are a newly established ship management company in Singapore. We manage a fleet of bulk carrier and car carriers. Our job is to run the ships economically and efficiently on behalf of owners of the vessel.
Updates

Project Deadline Extended
Reason: We are not satisfied by the designs as yet. Hence, we are extending the deadline further by 7 days.

Project Deadline Extended
Reason: No designs are up to our expectations

Project Deadline Extended

Target Market(s)

Our target market is various ship owners based all over the world especially in Japan and Europe. These ship owners are looking for third party managers to run their ships economically and efficiently.

Industry/Entity Type

It Company

Colors
32b7a4
33a6d7
00a88f
3276b5
0692cd
86cae6
86cfc6
ebf7f9
edf2f7

Requirements
Must have
• The brochure must have four pages (in form of a folder) with static information, photographs etc with a pocket designed inside to keep printed sheets containing dynamic information.
Write up on our company is attached herewith and also some photographs depicting our ships, crew and the training center.
Information for dynamic sheets is attached in a separate sheets.

```html
<!DOCTYPE html>
<html lang="en">
<head>
<meta charset="utf-8">
<title>KRTB Company Brochure – Inner Spread</title>
<link href="https://fonts.googleapis.com/css2?family=Open+Sans:wght@400;600;700&display=swap" rel="stylesheet">
<style>
  :root{
    --navy:#1f5fa6;
    --blue:#3276b5;
    --sky:#0692cd;
    --teal:#00a88f;
    --pale:#ebf7f9;
    --mist:#edf2f7;
    --ink:#3a4652;
    --stage:#e4e6e8;
    --paper:#ffffff;
  }
  *{box-sizing:border-box;margin:0;padding:0}
  html,body{width:1200px;height:846px;overflow:hidden}
  body{background:var(--stage);font-family:"Open Sans",Arial,sans-serif;color:var(--ink);position:relative}

  .spread{position:absolute;left:40px;top:40px;width:1120px;height:766px;display:flex;box-shadow:0 6px 18px rgba(0,0,0,.18)}
  .page{position:relative;width:560px;height:766px;background:var(--paper);overflow:hidden}
  .page--left{border-right:1px solid #d6dbe0}

  .top-band{position:absolute;top:0;left:0;right:0;height:22px;background:var(--navy)}
  .top-band::after{content:"";position:absolute;left:0;right:0;bottom:-3px;height:3px;background:var(--teal)}
  .bottom-band{position:absolute;bottom:0;left:0;right:0;height:14px;background:var(--navy)}
  .bottom-band::before{content:"";position:absolute;left:0;right:0;top:-3px;height:3px;background:var(--teal)}

  /* About */
  .about{position:absolute;left:28px;top:44px;width:362px}
  .section-title{font-weight:700;font-size:20px;color:var(--navy);letter-spacing:.3px;margin-bottom:6px}
  .about p{font-size:9.6px;line-height:13.6px;text-align:justify;margin-bottom:7px}
  .divider{position:absolute;left:400px;top:44px;bottom:30px;width:1px;background:#c9d3dc}

  .photo-strip{position:absolute;left:412px;top:44px;width:122px;display:flex;flex-direction:column;gap:8px}
  .photo{border-radius:2px}
  .photo-strip .photo{height:126px}
  .ph-carrier{background:linear-gradient(180deg,#b9d3e6 0%,#e9eef2 55%,#7a96ad 100%)}
  .ph-lifejackets{background:linear-gradient(180deg,#e9edf0 0%,#d2573f 55%,#b7412e 100%)}
  .ph-bulker{background:linear-gradient(180deg,#c5d2dc 0%,#9fb2c2 60%,#6f3b34 100%)}
  .ph-crew{background:linear-gradient(180deg,#7b8a70 0%,#5e6b5a 50%,#e3843e 100%)}
  .ph-hull{background:linear-gradient(180deg,#d7e1e8 0%,#8c4a3f 60%,#5d6b74 100%)}

  /* Services */
  .services{position:absolute;left:28px;top:508px;width:362px}
  .tab{display:inline-block;background:var(--navy);color:#fff;font-weight:700;font-size:14px;letter-spacing:.4px;padding:5px 26px 5px 12px;clip-path:polygon(0 0,88% 0,100% 100%,0 100%);border-bottom:3px solid var(--teal)}
  .services .lead{list-style:none;margin-top:12px}
  .services .lead li{display:flex;align-items:center;gap:8px;font-size:12.5px;font-weight:600;margin-bottom:6px;color:#2c3844}
  .services .intro{font-size:11px;font-weight:700;margin:6px 0 8px;color:#2c3844}
  .services .grid{list-style:none;display:grid;grid-template-columns:1fr 1fr;gap:6px 14px;padding-left:14px}
  .services .grid li{display:flex;align-items:center;gap:6px;font-size:10px;font-weight:600}
  .tick{flex:none}

  /* Right page */
  .office{position:absolute;left:30px;top:40px;width:500px;height:200px;background:linear-gradient(90deg,#6f7e8a 0%,#e9eaea 35%,#d6d2cc 70%,#a63a30 100%)}
  .initiatives{position:absolute;left:30px;top:262px;width:500px}
  .initiatives ul{list-style:none;margin-top:12px}
  .initiatives li{display:flex;gap:8px;font-size:10.2px;line-height:13.5px;margin-bottom:6px}
  .initiatives li svg{margin-top:2px}

  .commitment{position:absolute;left:0;right:0;bottom:14px;height:220px;background:var(--blue);border-top-left-radius:60px;border-top:3px solid var(--sky)}
  .commitment h2{position:absolute;left:30px;top:40px;color:#fff;font-size:20px;font-weight:700;letter-spacing:.3px}
  .commitment p{position:absolute;left:30px;top:74px;width:228px;color:#fff;font-size:10.4px;line-height:14.5px;text-align:justify}
  .ph-quay{position:absolute;right:26px;top:-20px;width:250px;height:190px;border:3px solid #fff;background:linear-gradient(180deg,#d6e1ea 0%,#b9c7d3 40%,#1c2430 62%,#a3322a 80%,#6e7a82 100%)}
</style>
</head>
<body>
<div class="spread">
  <section class="page page--left">
    <div class="top-band"></div>

    <article class="about">
      <h2 class="section-title">ABOUT US</h2>
      <p>Keel Ridge Tidewater Bureau Pte. Ltd. was established in Singapore in January 2012 as a ship management company to provide Quality service to like-minded ship owners and operators. The objective of the organization has been clear right from the beginning to concentrate on quality rather than quantity. The company has grown quite rapidly with this philosophy in the last 2 years from having 1 ship in April 2012 to 19 ships with full technical management at the end of 2013. KRTB is at the moment managing more than 1 million DWT tonnage, has 16 modern bulk carriers (52,000 DWT, 58,000 DWT, 82,000 DWT and 98,000 DWT) and 3 Car Carriers under their management with at least 4 more ships expected to join by the middle of this year. Apart from managing ships for Harunami Kaiun Co., Ltd. Japan who are partners in KRTB, the company has started to move into 3rd party Ship management activities and has bagged a few ships from other Singapore based Owners already. The credit for this growth goes to the strong team work, young and dedicated professionals and commitment that has been the hall mark of the organization.</p>
      <p>The company is headquartered in Central business district of Singapore and mitigated the cost disadvantage by opening a support office in Delhi, India and another office in Philippines where we also have a training center now.</p>
      <p>We are doing our bit to bring dignity to the Ship Management business where the Owners should see us as someone who adds value to the overall operation through clean and transparent activities and treat us as their trusted partners. We hope to build a legacy as many other big ship managers have and look forward to a great future ahead..</p>
    </article>

    <div class="divider"></div>

    <div class="photo-strip">
      <div class="photo ph-carrier" role="img" aria-label="Photo of a car carrier vessel at sea"></div>
      <div class="photo ph-lifejackets" role="img" aria-label="Photo of orange life jackets on a ship's deck"></div>
      <div class="photo ph-bulker" role="img" aria-label="Photo of a bulk carrier underway"></div>
      <div class="photo ph-crew" role="img" aria-label="Photo of crew in safety gear on a cargo deck"></div>
      <div class="photo ph-hull" role="img" aria-label="Photo of a bulk carrier hull in dry dock"></div>
    </div>

    <section class="services">
      <div class="tab">SERVICES OFFERED</div>
      <ul class="lead">
        <li><svg class="tick" width="14" height="12" viewBox="0 0 14 12"><path d="M1 6l4 4 8-9" fill="none" stroke="var(--ink)" stroke-width="2"/></svg>Ship Management</li>
        <li><svg class="tick" width="14" height="12" viewBox="0 0 14 12"><path d="M1 6l4 4 8-9" fill="none" stroke="var(--ink)" stroke-width="2"/></svg>Technical Solutions</li>
      </ul>
      <p class="intro">An array of technical solutions to the shipping world</p>
      <ul class="grid">
        <li><svg class="tick" width="11" height="10" viewBox="0 0 14 12"><path d="M1 6l4 4 8-9" fill="none" stroke="var(--ink)" stroke-width="2"/></svg>Technical Consultancy</li>
        <li><svg class="tick" width="11" height="10" viewBox="0 0 14 12"><path d="M1 6l4 4 8-9" fill="none" stroke="var(--ink)" stroke-width="2"/></svg>Docking</li>
        <li><svg class="tick" width="11" height="10" viewBox="0 0 14 12"><path d="M1 6l4 4 8-9" fill="none" stroke="var(--ink)" stroke-width="2"/></svg>New Building Supervision</li>
        <li><svg class="tick" width="11" height="10" viewBox="0 0 14 12"><path d="M1 6l4 4 8-9" fill="none" stroke="var(--ink)" stroke-width="2"/></svg>Condition Surveys</li>
        <li><svg class="tick" width="11" height="10" viewBox="0 0 14 12"><path d="M1 6l4 4 8-9" fill="none" stroke="var(--ink)" stroke-width="2"/></svg>Pre-Purchase Surveys</li>
        <li><svg class="tick" width="11" height="10" viewBox="0 0 14 12"><path d="M1 6l4 4 8-9" fill="none" stroke="var(--ink)" stroke-width="2"/></svg>Port Captaincy</li>
        <li><svg class="tick" width="11" height="10" viewBox="0 0 14 12"><path d="M1 6l4 4 8-9" fill="none" stroke="var(--ink)" stroke-width="2"/></svg>On-Site Supervision</li>
      </ul>
    </section>

    <div class="bottom-band"></div>
  </section>

  <section class="page page--right">
    <div class="top-band"></div>

    <div class="photo office" role="img" aria-label="Photo of the company office corridor and reception sign"></div>

    <section class="initiatives">
      <div class="tab">INITIATIVES</div>
      <ul>
        <li><svg class="tick" width="11" height="10" viewBox="0 0 14 12"><path d="M1 6l4 4 8-9" fill="none" stroke="var(--sky)" stroke-width="2"/></svg>Started own in house training institute in Manila to train our staff and keep them abreast of new developments in shipping industry.</li>
        <li><svg class="tick" width="11" height="10" viewBox="0 0 14 12"><path d="M1 6l4 4 8-9" fill="none" stroke="var(--sky)" stroke-width="2"/></svg>ECDIS installation started on board in order to ensure smooth transition to paperless navigation with proper training to ship staff in our training center.</li>
        <li><svg class="tick" width="11" height="10" viewBox="0 0 14 12"><path d="M1 6l4 4 8-9" fill="none" stroke="var(--sky)" stroke-width="2"/></svg>Commenced Internet facility on board all our vessels. 20 mb data being given free to each crew every month.</li>
        <li><svg class="tick" width="11" height="10" viewBox="0 0 14 12"><path d="M1 6l4 4 8-9" fill="none" stroke="var(--sky)" stroke-width="2"/></svg>Special emphasis on crew welfare with supply of fitness and entertainment equipment on board.</li>
        <li><svg class="tick" width="11" height="10" viewBox="0 0 14 12"><path d="M1 6l4 4 8-9" fill="none" stroke="var(--sky)" stroke-width="2"/></svg>Assistance like free telephone cards, Internet cards, cash donation provided to staff in case of a natural calamity in home country.</li>
      </ul>
    </section>

    <section class="commitment">
      <h2>COMMITMENT</h2>
      <p>The company believes that good training, motivation and emphasis on human values are essential for long term success. Consequently, the company is committed to providing an ideal working environment both in its offices and on ships.</p>
      <div class="ph-quay" role="img" aria-label="Photo of a bulk carrier moored at a port quay with cranes"></div>
    </section>

    <div class="bottom-band"></div>
  </section>
</div>
</body>
</html>
```